Catering Menu Package

I currently have a complete menu package, which we have redesigned as far as content, now I need to it put together in a catalog type format. It is essentially 10-12 pages in length, and will be sent for print production. Upon receiving a final edit
Updates

I have added an example gif to the project.

I did this free hand this basically what I am looking for. please change text and type to whatever you think would look best. This is a total rough design so, feel free to change any and everything. The text for the page is on the word documents. If you need more images let me know I am in the process of getting as many images uploaded for your use.

Project Deadline Extended
Reason: I figured we got a late jump with questions, so i am extending a few days .

Target Market(s)

The target market is business who wish to have catered luncheons, breakfasts , meetings

Industry/Entity Type

Catering

Requirements
Must have
• I have attached a copy of the text that what we want in the package, our logo, and i have also attached a catering package of another company to give you an idea what the finished product will be
Should not have
• It should not look identical to the example catering packages, these are for some inspiration we want our own design with the same type of look and feel

```html
<!DOCTYPE html>
<html lang="en">
<head>
<meta charset="utf-8">
<title>Sample Cocktail Hour &amp; Reception Menus</title>
<link href="https://fonts.googleapis.com/css2?family=Crimson+Text:ital,wght@0,400;0,600;1,400&family=Parisienne&display=swap" rel="stylesheet">
<style>
  :root {
    --ink: #2b211c;
    --accent: #9a5a2e;
    --muted: #6e625a;
    --strip-top: #f7f3ef;
    --strip-bottom: #dccfc3;
    --panel-top: #ffffff;
    --panel-bottom: #f1eeeb;
    --title: #3a302a;
  }
  * { margin: 0; padding: 0; box-sizing: border-box; }
  html, body { width: 1200px; height: 927px; overflow: hidden; }
  body {
    position: relative;
    font-family: "Crimson Text", Georgia, serif;
    color: var(--ink);
    background: linear-gradient(180deg, var(--strip-top) 0%, var(--strip-top) 40%, var(--strip-bottom) 100%);
  }
  .panel {
    position: absolute;
    left: 182px; top: 0;
    width: 1018px; height: 927px;
    background: linear-gradient(160deg, var(--panel-top) 0%, var(--panel-top) 55%, var(--panel-bottom) 100%);
    box-shadow: -3px 0 8px rgba(80, 60, 40, 0.12);
  }
  .brand {
    position: absolute;
    left: 28px; top: 24px;
    width: 132px;
    text-align: center;
    color: var(--ink);
    font-weight: 600;
    font-size: 24px;
    line-height: 26px;
    text-transform: lowercase;
  }
  .brand-mark {
    display: block;
    width: 96px; height: 96px;
    margin: 0 auto 14px;
    border-radius: 50%;
    background: var(--ink);
  }
  .page-title {
    position: absolute;
    left: 197px; top: 56px;
    font-family: "Parisienne", cursive;
    font-weight: 400;
    font-size: 38px;
    color: var(--title);
    text-shadow: 1px 2px 3px rgba(0,0,0,0.18);
    white-space: nowrap;
  }
  .menu { position: absolute; }
  .menu-sampler { left: 197px; top: 140px; width: 460px; }
  .menu-artisan { left: 690px; top: 200px; width: 480px; }
  .menu-name {
    font-family: "Parisienne", cursive;
    font-weight: 400;
    font-size: 36px;
    line-height: 48px;
    color: var(--title);
    text-shadow: 1px 2px 3px rgba(0,0,0,0.18);
    margin-bottom: 22px;
  }
  .menu-artisan .menu-name { margin-bottom: 10px; }
  .menu-intro {
    font-style: italic;
    color: var(--muted);
    font-size: 18px;
    line-height: 24px;
    margin-bottom: 14px;
  }
  .menu-item {
    font-size: 19px;
    line-height: 24.3px;
    margin-bottom: 12px;
  }
  .menu-item.accent { color: var(--accent); }
  .platter-photo {
    position: absolute;
    left: 438px; top: 484px;
    width: 184px; height: 184px;
    border-radius: 50%;
    background: radial-gradient(circle at 45% 45%, #c9a063 0%, #a8773f 45%, #6d4626 100%);
    box-shadow: 3px 5px 10px rgba(0,0,0,0.3);
  }
</style>
</head>
<body>
  <div class="brand">
    <span class="brand-mark"></span>
    fernhill caterers
  </div>

  <main class="panel"></main>

  <h1 class="page-title">Sample Cocktail Hour &amp; Reception Menus</h1>

  <section class="menu menu-sampler">
    <h2 class="menu-name">The Sampler</h2>
    <p class="menu-item">Assorted Miniature Sandwiches</p>
    <p class="menu-item accent">Oven Roasted Turkey, Black Forest Ham &amp; Roasted<br>Top Round of Beef</p>
    <p class="menu-item">Served on Artisan rolls &amp; fresh baked baguette</p>
    <p class="menu-item accent">Served with Mayonaise, Mustard, Dijon, &amp;<br>Horseradish</p>
    <p class="menu-item">Rotisserie Roasted Chicken Drummies<br>&amp; Wing Sections</p>
    <p class="menu-item accent">Served with Sweet &amp; Sour Hot Sauce<br>&amp; Chipotle Ranch</p>
    <p class="menu-item">With Celery &amp; Carrot Stalks</p>
    <p class="menu-item accent">Cranberry BBQ Meatballs</p>
    <p class="menu-item">Fresh Fruit &amp; Melon Display</p>
    <p class="menu-item accent">Vegetable Pasta Salad</p>
    <p class="menu-item">Maryland Crab Dip</p>
    <p class="menu-item accent">Served with Gourmet Crackers</p>
  </section>

  <div class="platter-photo" role="img" aria-label="Round wooden board of cheeses, cured sausage, dried fruit and nuts"></div>

  <section class="menu menu-artisan">
    <h2 class="menu-name">The Artisan</h2>
    <p class="menu-intro">An Artfully Displayed Hors'doeuvre Table<br>including the following:</p>
    <p class="menu-item">Artisan Rolls &amp; Breads</p>
    <p class="menu-item accent">Lavosh, Assorted Gourmet Crackers, &amp; Crostinis Pita</p>
    <p class="menu-item">Bread Wedges &amp;&nbsp; Baguette Loafs</p>
    <p class="menu-item accent">Fresh Grapes &amp; Strawberries</p>
    <p class="menu-item">Seasonal fruit</p>
    <p class="menu-item accent">Garden Fresh Vegetables</p>
    <p class="menu-item">Grilled &amp; Marinated in Aged Imported<br>Balsamic Vinegar</p>
    <p class="menu-item accent">A Variety of Artisan Cheeses, including but not<br>limited to Cheddar, Havarti, Goat Cheese, Gorgonzola,<br>Smoked Gouda, Pepper-Jack, &amp; Brie accompanied with<br>Assorted Dried Fruit &amp; Nuts</p>
    <p class="menu-item">Various Imported Olives &amp; Pickled Vegetables</p>
    <p class="menu-item accent">Aged Salami, Italian Hams, &amp; Pepperoni</p>
    <p class="menu-item">Hummus &amp; Olive Tapenades</p>
    <p class="menu-item accent">Infused Olive Oils</p>
  </section>
</body>
</html>
```